Cobalt Ridge Electric Needs A Logo Design

We need a logo for my new company based out of Sacramento, Ca called Cobalt Ridge Electric. The name says it all, my electrical contracting business provides "Cobalt Ridge Professional Work" I'm open to any colors that pop and customers to say Wow. I would love to print my cards on metal.

Industry/Entity Type

Business

Contact Information for Business Card

The card needs to have as follows
Name of company: Cobalt Ridge Electric
My Name: Marco Delvane
Phone # 916-555-0173
CL# 2049381
Email: cobaltridgeelectric@mailnest.example
and a slogan that represent "COBALT RIDGE"

Requirements
Must have
• The card needs to have as follows
• Name of company: Cobalt Ridge Electric
• My Name : Marco Delvane
• Phone # 916-555-0173
• CL# 2049381
• Email: cobaltridgeelectric@mailnest.example
• and a slogan that represent "COBALT RIDGE"
Nice to have
• popping colors
• electrical Arcing

```html
<!DOCTYPE html>
<html lang="en">
<head>
<meta charset="utf-8">
<title>Cobalt Ridge Electric — Business Card</title>
<link rel="stylesheet" href="https://fonts.googleapis.com/css2?family=Open+Sans:wght@400;600;700&family=Exo+2:wght@500;600&display=swap">
<style>
  :root {
    --cobalt: #0567b3;
    --white: #ffffff;
    --ink: #3a3a3a;
    --backdrop: #ecebe8;
    --card-shadow: rgba(0, 0, 0, 0.16);
  }
  * { box-sizing: border-box; margin: 0; padding: 0; }
  html, body {
    width: 1200px;
    height: 900px;
    overflow: hidden;
    background: var(--backdrop);
  }
  .stage { position: relative; width: 1200px; height: 900px; }

  .card {
    position: absolute;
    background: var(--white);
    box-shadow: 0 4px 14px var(--card-shadow);
    overflow: hidden;
  }

  /* Front side */
  .card--front { left: 238px; top: 60px; width: 555px; height: 344px; }
  .front-band {
    position: absolute; left: 0; top: 0;
    width: 100%; height: 292px;
    background: var(--cobalt);
    overflow: hidden;
  }
  .front-band__disc {
    position: absolute;
    left: 332px; top: -38px;
    width: 250px; height: 250px;
    border-radius: 50%;
    background: var(--white);
  }
  .holder-name {
    position: absolute; left: 34px; top: 64px;
    font: 600 24px/1 "Open Sans", sans-serif;
    color: var(--white);
  }
  .contact-list {
    position: absolute; left: 34px; top: 197px;
    list-style: none;
    font: 400 15px/20px "Open Sans", sans-serif;
    color: var(--white);
  }
  .contact-list li { display: flex; align-items: center; gap: 8px; }
  .contact-list svg { width: 12px; height: 12px; fill: var(--white); flex: none; }
  .slogan {
    position: absolute; left: 0; right: 0; top: 308px;
    text-align: center;
    font: 500 18px/1 "Exo 2", sans-serif;
    letter-spacing: 1.6px;
    color: var(--ink);
    text-transform: uppercase;
  }

  /* Back side */
  .card--back { left: 457px; top: 518px; width: 560px; height: 343px; }
  .brand-disc {
    position: absolute; left: 236px; top: 80px;
    width: 88px; height: 88px;
    border-radius: 50%;
    background: var(--cobalt);
  }
  .brand-name {
    position: absolute; left: 0; right: 0; top: 198px;
    text-align: center;
    font: 600 38px/1 "Exo 2", sans-serif;
    letter-spacing: 1px;
    color: var(--cobalt);
    text-transform: uppercase;
  }
  .brand-name span { display: block; font-size: 24px; letter-spacing: 3px; margin-top: 8px; }
</style>
</head>
<body>
<main class="stage">

  <section class="card card--front" aria-label="Business card front">
    <div class="front-band">
      <div class="front-band__disc"></div>
      <p class="holder-name">Marco Delvane</p>
      <ul class="contact-list">
        <li>
          <svg viewBox="0 0 24 24" aria-hidden="true"><path d="M6.6 10.8a15.1 15.1 0 0 0 6.6 6.6l2.2-2.2a1 1 0 0 1 1-.25 11.4 11.4 0 0 0 3.6.57 1 1 0 0 1 1 1V20a1 1 0 0 1-1 1A17 17 0 0 1 3 4a1 1 0 0 1 1-1h3.5a1 1 0 0 1 1 1c0 1.25.2 2.45.57 3.57a1 1 0 0 1-.25 1z"/></svg>
          916-555-0173
        </li>
        <li>
          <svg viewBox="0 0 24 24" aria-hidden="true"><path d="M7 1h10a2 2 0 0 1 2 2v18a2 2 0 0 1-2 2H7a2 2 0 0 1-2-2V3a2 2 0 0 1 2-2zm0 4v13h10V5z"/></svg>
          2049381
        </li>
        <li>
          <svg viewBox="0 0 24 24" aria-hidden="true"><path d="M2 5h20v14H2zm2 2v.5l8 5 8-5V7l-8 5z"/></svg>
          cobaltridgeelectric@mailnest.example
        </li>
      </ul>
    </div>
    <p class="slogan">Cobalt Ridge Professional Work</p>
  </section>

  <section class="card card--back" aria-label="Business card back">
    <div class="brand-disc"></div>
    <p class="brand-name">Cobalt Ridge<span>Electric</span></p>
  </section>

</main>
</body>
</html>
```